Website for "Bright Morrow Ltd" cleaning bsuiness

We require a website to expose our business to the local market. We want to provide background on who we are and what we do but in an easily digestible way. We clean domestic and commercial premises and want to provide a list of all of our services to potential customers. We operate out of Warrington in the UK.

We would like the website to be animated in some way so that the experience of using it is not dull or mundane. This website needs to be an extension of our company.

Target Market(s)

30 - 60 year olds for Domestic plus commercial clients

Industry/Entity Type

Cleaning Service

Coding

Coded - Design and coding required

Number of Pages Required

4 page

Font styles to use
Sans Serif

Colors
0455a3
3176b5
85acd3
cfdeed
ffffff
000000
1b1b1b
c8c8c8
757575

Requirements
Must have
• Logo which has been provided. Theme based around the logo and its colours. Simple layout to avoid confusion.
Nice to have
• Animations where possible to impress the customer.
Should not have
• any pictures of cleaning equipment, fairies, maids etc

```html
<!DOCTYPE html>
<html lang="en">
<head>
<meta charset="utf-8">
<title>Bright Morrow Ltd – Professional Cleaning Services</title>
<link rel="stylesheet" href="https://fonts.googleapis.com/css2?family=Roboto+Condensed:wght@400;700&family=Roboto:wght@400;500;700&display=swap">
<style>
:root{
  --brand:#0455a3;
  --brand-mid:#3176b5;
  --brand-soft:#85acd3;
  --brand-pale:#cfdeed;
  --white:#ffffff;
  --black:#000000;
  --ink:#1b1b1b;
  --line:#c8c8c8;
  --muted:#757575;
  --heading:#4a4f63;
  --footer-base:#03498c;
}
*{box-sizing:border-box;margin:0;padding:0}
html,body{width:1200px;height:2571px;overflow:hidden}
body{position:relative;background:var(--white);font-family:"Roboto",Arial,sans-serif;color:var(--ink)}
.abs{position:absolute}
.cond{font-family:"Roboto Condensed","Arial Narrow",sans-serif}

/* header */
.site-header{left:0;top:0;width:1200px;height:120px;background:var(--white)}
.brand{left:100px;top:30px;display:flex;align-items:center;gap:12px}
.brand-dot{width:46px;height:46px;border-radius:50%;background:var(--brand)}
.brand-name{font-family:"Roboto",Arial,sans-serif;font-weight:700;font-size:26px;color:var(--brand);line-height:1}
.call{left:684px;top:18px;display:flex;align-items:center;gap:10px}
.call-label{font-size:12px;color:var(--muted)}
.call-number{font-size:16px;color:var(--ink)}
.book-btn{left:842px;top:24px;width:144px;height:31px;background:var(--brand-mid);color:var(--white);font-size:12.5px;font-weight:500;display:flex;align-items:center;justify-content:center;letter-spacing:.3px}
.social-dot{top:26px;width:28px;height:28px;border-radius:50%}
.main-nav{left:507px;top:74px;display:flex;gap:0;font-size:13px;color:#555}
.main-nav span{padding:7px 13px;height:30px;display:block}
.main-nav .current{border:1px solid var(--brand-mid);color:var(--brand-mid)}

/* hero */
.hero{left:0;top:120px;width:1200px;height:535px;background:linear-gradient(180deg,#6f6a62 0%,#8f877c 35%,#5a4434 70%,#3a2a20 100%)}
.hero-title{left:0;top:333px;width:1200px;text-align:center;color:var(--white);font-weight:700;font-size:50px;line-height:53px;text-shadow:0 2px 6px rgba(0,0,0,.4)}
.hero-dots{left:571px;top:465px;display:flex;gap:8px}
.hero-dots i{width:14px;height:14px;border-radius:50%;border:2px solid var(--white);display:block}
.hero-dots i.on{background:var(--white)}

/* intro */
.intro-photo{width:182px;height:182px;border-radius:50%;border:3px solid var(--brand-pale)}
.intro-title{font-size:23px;color:var(--ink);letter-spacing:.3px}
.intro-text{width:270px;font-size:11.5px;line-height:19px;color:var(--muted)}
.read-more{width:94px;height:31px;border:1px solid var(--brand-mid);color:var(--brand-mid);font-size:11.5px;display:flex;align-items:center;justify-content:center}

/* services */
.services{left:0;top:957px;width:1200px;height:469px;background:linear-gradient(180deg,#3a7bbb,#2f6fae)}
.section-title{left:0;width:1200px;text-align:center;font-size:30px}
.service-card{top:1071px;width:235px;height:263px;background:var(--white);padding:4px}
.service-img{width:227px;height:216px}
.service-name{text-align:center;font-size:17px;color:#555;margin-top:11px}
.ring-btn{top:1366px;width:24px;height:24px;border-radius:50%;border:1px solid var(--white)}

/* blog */
.blog-img{top:1550px;width:309px;height:173px}
.date-box{top:1747px;width:48px;height:56px;background:var(--brand-mid);color:var(--white);text-align:center}
.date-day{font-size:20px;font-weight:700;padding-top:6px;line-height:22px}
.date-mon{font-size:10px;margin-top:6px}
.blog-title{top:1745px;font-size:16px;color:#444}
.blog-text{top:1773px;width:250px;font-size:11px;line-height:19px;color:var(--muted)}

/* testimonials */
.testimonials{left:0;top:1887px;width:1200px;height:345px;background:linear-gradient(180deg,#1e1a18,#2e2824 55%,#1a1715)}
.quote-text{left:218px;top:2022px;width:776px;text-align:center;color:var(--white);font-size:11.5px;line-height:20px}
.quote-name{left:0;top:2102px;width:1200px;text-align:center;color:var(--white);font-style:italic;font-size:18px}
.quote-bars{left:552px;top:2159px;display:flex;gap:6px}
.quote-bars i{width:28px;height:3px;background:#777;display:block}
.quote-bars i.on{background:var(--white)}

/* footer */
.site-footer{left:0;top:2232px;width:1200px;height:281px;background:var(--brand)}
.footer-brand{left:99px;top:2282px;display:flex;align-items:center;gap:10px}
.footer-brand .brand-dot{background:var(--white);width:40px;height:40px}
.footer-brand .brand-name{color:var(--white);font-size:24px}
.footer-text{color:var(--white);font-size:13px;line-height:20px}
.footer-heading{top:2272px;color:var(--white);font-size:17px;font-weight:500}
.quick-links li{list-style:none;color:var(--white);font-size:12px;height:24px;display:flex;align-items:center;gap:12px}
.social-list li{list-style:none;color:var(--white);font-size:14px;height:36px;display:flex;align-items:center;gap:10px}
.social-ring{width:27px;height:27px;border-radius:50%;border:1.5px solid var(--white)}
.field{border:1px solid var(--white);color:var(--white);font-size:11px;padding:10px 11px}
.submit{left:801px;top:2433px;width:107px;height:36px;border:1px solid var(--white);color:var(--white);font-size:14px;font-weight:700;display:flex;align-items:center;justify-content:center}
.copyright-bar{left:0;top:2513px;width:1200px;height:58px;background:var(--footer-base);color:var(--white);font-size:12px;display:flex;align-items:center;justify-content:center}
</style>
</head>
<body>

<header class="site-header abs">
  <div class="brand abs"><span class="brand-dot"></span><span class="brand-name">Bright Morrow Ltd</span></div>
  <div class="call abs">
    <svg width="30" height="30" viewBox="0 0 30 30"><circle cx="15" cy="15" r="13.5" fill="none" stroke="#757575" stroke-width="1.5"/><path d="M10 9c1-1 2-1 2.6 0l1.4 2.4c.4.7.2 1.3-.4 1.8l-.8.6c.6 1.6 2 3 3.6 3.6l.6-.8c.5-.6 1.1-.8 1.8-.4l2.4 1.4c1 .6 1 1.6 0 2.6-1.4 1.4-3.6 1.4-6.2-.4-2-1.4-3.6-3-5-5-1.8-2.6-1.8-4.8-.4-6.2z" fill="#757575"/></svg>
    <div><div class="call-label">Call Us</div><div class="call-number">+1200 555 018</div></div>
  </div>
  <div class="book-btn abs">BOOK APPOINTMENT</div>
  <span class="social-dot abs" style="left:1001px;background:#3b5b98"></span>
  <span class="social-dot abs" style="left:1035px;background:#3aa6dd"></span>
  <span class="social-dot abs" style="left:1071px;background:#d9352a"></span>
  <nav class="main-nav abs">
    <span class="current">HOME</span><span>ABOUT US</span><span>OUR SERVICES</span><span>TERMS &amp; CONDITIONS</span><span>NEWS</span><span>CONTACT US</span>
  </nav>
</header>

<section class="hero abs" role="img" aria-label="Bright living room with wooden floor, armchairs and a fireplace"></section>
<h1 class="hero-title abs cond">PROFESSIONAL<br>CLEANING SERVICES</h1>
<div class="hero-dots abs"><i class="on"></i><i></i><i></i></div>

<section class="intro">
  <div class="intro-photo abs" style="left:98px;top:713px;background:linear-gradient(135deg,#cfdeed,#3176b5 60%,#0f3e78)" role="img" aria-label="Glass office tower seen from below"></div>
  <h2 class="intro-title abs cond" style="left:303px;top:718px">WHO WE ARE</h2>
  <p class="intro-text abs" style="left:303px;top:755px">Sed ut perspiciatis unde omnis iste natus error sit voluptatem accusantium doloremque laudantium, totam rem aperiam, eaque ipsa quae ab illo inventore veritatis et quasi</p>
  <div class="read-more abs" style="left:303px;top:852px">READ MORE</div>

  <div class="intro-photo abs" style="left:638px;top:713px;background:radial-gradient(circle at 50% 40%,#8fb9dd,#2f6da9 70%,#1c3f6c)" role="img" aria-label="Business man in a suit with folded arms"></div>
  <h2 class="intro-title abs cond" style="left:842px;top:718px">WHAT WE DO</h2>
  <p class="intro-text abs" style="left:842px;top:755px">Sed ut perspiciatis unde omnis iste natus error sit voluptatem accusantium doloremque laudantium, totam rem aperiam, eaque ipsa quae ab illo inventore veritatis et quasi</p>
  <div class="read-more abs" style="left:842px;top:852px">READ MORE</div>
</section>

<section class="services abs" role="img" aria-label="Faded blue office interior behind the services"></section>
<h2 class="section-title abs cond" style="top:1006px;color:var(--white)">OUR SERVICES</h2>
<div class="service-card abs" style="left:99px"><div class="service-img" style="background:linear-gradient(180deg,#e9e9e9,#c9c6c2)" role="img" aria-label="White modern living room"></div><div class="service-name">Clean Domestic</div></div>
<div class="service-card abs" style="left:355px"><div class="service-img" style="background:linear-gradient(180deg,#6aa4dc,#a9c4d8 55%,#8c8c88)" role="img" aria-label="Glass office building under blue sky"></div><div class="service-name">Commercial Premises</div></div>
<div class="service-card abs" style="left:610px"><div class="service-img" style="background:linear-gradient(180deg,#e4e2de,#9d8f7e 60%,#5b3f2c)" role="img" aria-label="Living room with armchairs and wooden floor"></div><div class="service-name">Clean Domestic</div></div>
<div class="service-card abs" style="left:864px"><div class="service-img" style="background:linear-gradient(135deg,#4f86c6,#c2683c 45%,#9aa7ad)" role="img" aria-label="Modern commercial building with glass front"></div><div class="service-name">Commercial Premises</div></div>
<div class="ring-btn abs" style="left:572px"><svg width="22" height="22" viewBox="0 0 22 22"><path d="M13 6l-5 5 5 5" fill="none" stroke="#fff" stroke-width="1.5"/></svg></div>
<div class="ring-btn abs" style="left:602px"><svg width="22" height="22" viewBox="0 0 22 22"><path d="M9 6l5 5-5 5" fill="none" stroke="#fff" stroke-width="1.5"/></svg></div>

<section class="blog">
  <h2 class="section-title abs cond" style="top:1481px;color:var(--heading)">LATEST BLOG</h2>
  <div class="blog-img abs" style="left:99px;background:linear-gradient(135deg,#f1ede8,#b9a48c 55%,#4a4a4a)" role="img" aria-label="Woman standing in a bright office"></div>
  <div class="blog-img abs" style="left:446px;background:linear-gradient(180deg,#cfe1ee,#7b96ac 55%,#32404c)" role="img" aria-label="Colleagues working at laptops under pendant lights"></div>
  <div class="blog-img abs" style="left:792px;background:linear-gradient(135deg,#ecebe8,#b3afa8 60%,#3b3937)" role="img" aria-label="Minimal lounge with sofa and stone fireplace"></div>

  <div class="date-box abs" style="left:99px"><div class="date-day">02</div><div class="date-mon">JUN</div></div>
  <div class="blog-title abs" style="left:159px">Sed ut perspiciatis unde omnis iste</div>
  <p class="blog-text abs" style="left:159px">Lorem ipsum dolor sit amet, consectetur adipg elit, sed do eiusmod tempor incididunt</p>

  <div class="date-box abs" style="left:446px"><div class="date-day">02</div><div class="date-mon">JUN</div></div>
  <div class="blog-title abs" style="left:506px">Sed ut perspiciatis unde omnis iste</div>
  <p class="blog-text abs" style="left:506px">Lorem ipsum dolor sit amet, consectetur adipg elit, sed do eiusmod tempor incididunt</p>

  <div class="date-box abs" style="left:792px"><div class="date-day">02</div><div class="date-mon">JUN</div></div>
  <div class="blog-title abs" style="left:852px">Sed ut perspiciatis unde omnis iste</div>
  <p class="blog-text abs" style="left:852px">Lorem ipsum dolor sit amet, consectetur adipg elit, sed do eiusmod tempor incididunt</p>
</section>

<section class="testimonials abs" role="img" aria-label="Dim interior with a plant and tall windows"></section>
<h2 class="section-title abs cond" style="top:1961px;color:var(--white)">TESTIMONIALS</h2>
<svg class="abs" style="left:206px;top:2012px" width="14" height="12" viewBox="0 0 14 12"><path d="M1 10l3-8M8 10l3-8" stroke="#fff" stroke-width="1.6"/></svg>
<p class="quote-text abs">Sed ut perspiciatis unde omnis iste natus error sit voluptatem accusantium doloremque laudantium, totam rem aperiam, eaque ipsa quae ab illo inventore veritatis et quasi architecto beatae vitae dicta sunt explicabo. Nemo enim ipsam voluptatem quia voluptas sit aspernatur aut odit aut fugit, sed quia consequuntur magni dolores eos qui ratione voluptatem</p>
<div class="quote-name abs">Harriet Colby – Bright Morrow</div>
<div class="quote-bars abs"><i class="on"></i><i></i><i></i></div>

<footer class="site-footer abs"></footer>
<div class="footer-brand abs"><span class="brand-dot"></span><span class="brand-name">Bright Morrow Ltd</span></div>
<p class="footer-text abs" style="left:99px;top:2363px;width:240px">24 Morrow Lane, Unit 12 | Warrington, WA1 2AB</p>
<div class="footer-text abs" style="left:99px;top:2419px;display:flex;align-items:center;gap:14px">
  <svg width="20" height="20" viewBox="0 0 20 20"><path d="M4 2c1-1 2-1 2.6 0l1.6 2.6c.4.7.2 1.3-.4 1.8l-1 .8c.8 2 2.4 3.6 4.4 4.4l.8-1c.5-.6 1.1-.8 1.8-.4l2.6 1.6c1 .6 1 1.6 0 2.6-1.6 1.6-4 1.6-7-.6-2-1.4-3.6-3-5-5C2.4 6 2.4 3.6 4 2z" fill="none" stroke="#fff" stroke-width="1.2"/></svg>
  <span>Phone : (415) 555-0142</span>
</div>
<div class="footer-text abs" style="left:99px;top:2443px;display:flex;align-items:center;gap:14px">
  <svg width="20" height="16" viewBox="0 0 20 16"><rect x="1" y="2" width="18" height="12" fill="none" stroke="#fff" stroke-width="1.2"/><path d="M1 2l9 7 9-7" fill="none" stroke="#fff" stroke-width="1.2"/></svg>
  <span>Email: info@brightmorrow.example</span>
</div>

<h3 class="footer-heading abs cond" style="left:413px">QUICK LINKS</h3>
<ul class="quick-links abs" style="left:413px;top:2314px">
  <li><svg width="6" height="8" viewBox="0 0 6 8"><path d="M0 0l6 4-6 4z" fill="#fff"/></svg>HOME</li>
  <li><svg width="6" height="8" viewBox="0 0 6 8"><path d="M0 0l6 4-6 4z" fill="#fff"/></svg>ABOUT US</li>
  <li><svg width="6" height="8" viewBox="0 0 6 8"><path d="M0 0l6 4-6 4z" fill="#fff"/></svg>SUPPLIES</li>
  <li><svg width="6" height="8" viewBox="0 0 6 8"><path d="M0 0l6 4-6 4z" fill="#fff"/></svg>SERVICES</li>
  <li><svg width="6" height="8" viewBox="0 0 6 8"><path d="M0 0l6 4-6 4z" fill="#fff"/></svg>BLOG</li>
  <li><svg width="6" height="8" viewBox="0 0 6 8"><path d="M0 0l6 4-6 4z" fill="#fff"/></svg>CONTACT</li>
</ul>

<h3 class="footer-heading abs cond" style="left:610px">SOCIAL</h3>
<ul class="social-list abs" style="left:610px;top:2310px">
  <li><span class="social-ring"></span>Linkup</li>
  <li><span class="social-ring"></span>Chirper</li>
  <li><span class="social-ring"></span>Gather+</li>
  <li><span class="social-ring"></span>Streamly</li>
</ul>

<h3 class="footer-heading abs cond" style="left:801px">QUICK ENQUIRY</h3>
<div class="field abs" style="left:801px;top:2313px;width:145px;height:37px">Name</div>
<div class="field abs" style="left:955px;top:2313px;width:145px;height:37px">Phone</div>
<div class="field abs" style="left:801px;top:2357px;width:299px;height:69px">Message</div>
<div class="submit abs">SUBMIT</div>

<div class="copyright-bar abs">Copyright © 2016 Bright Morrow. All rights reserved.</div>

</body>
</html>
```